Treatment Info-Graphic Poster

22 x 28 poster. We need a design for a poster to hang in our treatment rooms that quickly compares different treatments we offer and sets expectations for the patient. Attached is something I very quickly created on Excel, but we would like one that matches our company colors and looks much more polished. I have attached a info-graphic we have had designed prior for reference.

Target Market(s)

Osteoarthritis of the knee patients treatment comparison info graphic for poster

Font styles to use
Serif

Colors
85cae6
f78f20

Requirements
Must have
• Branded treatment comparison table
Nice to have
• Treatment graphics

```html
<!DOCTYPE html>
<html lang="en">
<head>
<meta charset="utf-8">
<title>kinetra – Osteoarthritis of the knee treatment comparison</title>
<link href="https://fonts.googleapis.com/css2?family=Arvo:wght@400;700&family=Nunito+Sans:wght@400;600;700&display=swap" rel="stylesheet">
<style>
  :root{
    --cream:#fdf1e0;
    --page:#ffffff;
    --teal:#45d0c5;
    --orange:#ff7f00;
    --ink:#333333;
    --dark:#343434;
    --grey:#e4e4e4;
    --white:#ffffff;
  }
  *{box-sizing:border-box;margin:0;padding:0}
  html,body{width:847px;height:1200px;overflow:hidden;background:var(--page)}
  .poster{position:relative;width:847px;height:1200px;background:var(--cream);border-radius:44px;
    font-family:"Arvo",Georgia,serif;color:var(--ink)}

  .brand{position:absolute;left:66px;top:70px;width:218px;height:104px;display:flex;align-items:center;justify-content:center}
  .brand-name{font-family:"Arvo",Georgia,serif;font-weight:700;font-size:56px;color:var(--teal);letter-spacing:-1px}
  .tagline{position:absolute;left:66px;width:218px;text-align:center;top:188px;font-family:"Nunito Sans",Arial,sans-serif;font-size:16px;color:#222}

  .title{position:absolute;left:330px;top:94px;font-weight:700;font-size:32.5px;line-height:41px;color:var(--ink);white-space:nowrap}

  .table{position:absolute;left:34px;top:259px;display:grid;
    grid-template-columns:249px repeat(4,128.5px);
    grid-template-rows:46px 134px repeat(11,51.6px)}

  .th{display:flex;align-items:center;gap:6px;padding:0 6px;color:var(--white);font-weight:700;font-size:10.5px;line-height:13px;white-space:nowrap}
  .th.teal{background:var(--teal)} .th.orange{background:var(--orange)}
  .th.first{border-top-left-radius:14px}
  .th.last{border-top-right-radius:22px}
  .th-icon{flex:none;width:26px;height:26px}

  .options{padding:12px 4px 0 6px;font-family:"Nunito Sans",Arial,sans-serif;font-size:6.8px;line-height:8px;color:#111;white-space:nowrap}
  .options.grey{background:var(--grey)} .options.white{background:var(--white)}
  .option{position:relative;padding-left:8px}
  .option::before{content:"";position:absolute;left:0;top:2px;width:4px;height:4px;border-radius:50%;background:var(--orange)}
  .option.plain{padding-left:0} .option.plain::before{display:none}
  .grade{color:var(--teal);padding-left:8px;margin:4px 0 6px}
  .grade.flush{padding-left:0}

  .label{background:var(--dark);color:var(--white);display:flex;align-items:center;border-radius:10px 0 0 10px;
    border-bottom:2px solid var(--cream);font-size:11.4px;line-height:15.5px;font-weight:700;white-space:nowrap}
  .label-icon{flex:none;width:97px;display:flex;align-items:center;justify-content:flex-start;padding-left:15px}
  .label-icon svg{width:60px;height:30px}

  .cell{display:flex;align-items:center;justify-content:center;border-bottom:1.5px solid rgba(255,255,255,.28)}
  .cell.teal{background:var(--teal)} .cell.orange{background:var(--orange)}
  .tick{width:46px;height:36px}

  .disclaimer{position:absolute;left:86px;width:676px;top:1039px;text-align:center;font-size:19px;line-height:23.6px;color:#1e1e1e}
  .rule{position:absolute;left:260px;top:1145px;width:310px;height:4px}
</style>
</head>
<body>
<main class="poster">
  <div class="brand"><span class="brand-name">kinetra</span></div>
  <p class="tagline">Move freely again.</p>
  <h1 class="title">Osteoarthritis of the knee<br>treatment comparison</h1>

  <svg width="0" height="0" style="position:absolute">
    <defs>
      <symbol id="tick" viewBox="0 0 46 36"><path d="M5 19 L17 30 L41 6" fill="none" stroke="#fff" stroke-width="8" stroke-linecap="round" stroke-linejoin="round"/></symbol>
    </defs>
  </svg>

  <section class="table" aria-label="Treatment comparison table">
    <div></div>
    <div class="th teal first">
      <svg class="th-icon" viewBox="0 0 26 26"><circle cx="13" cy="13" r="12" fill="#fff"/><path d="M7 19 L17 9 M15 7 L19 11" stroke="#45d0c5" stroke-width="2.4" stroke-linecap="round"/></svg>
      <span>Hyaluronic<br>Acid (HA)</span></div>
    <div class="th orange">
      <svg class="th-icon" viewBox="0 0 26 26"><circle cx="13" cy="13" r="12" fill="#fff"/><circle cx="10" cy="15" r="3.5" fill="#45d0c5"/><circle cx="16" cy="10" r="3" fill="#ff7f00"/></svg>
      <span>Platelet Rich<br>Plasma (PRP)</span></div>
    <div class="th teal">
      <svg class="th-icon" viewBox="0 0 26 26"><circle cx="13" cy="13" r="12" fill="#fff"/><path d="M9 6 C17 10 9 16 17 20 M17 6 C9 10 17 16 9 20" stroke="#ff7f00" stroke-width="1.8" fill="none"/></svg>
      <span>Stem Cell<br>Therapy &amp; PRP</span></div>
    <div class="th orange last">
      <svg class="th-icon" viewBox="0 0 26 26"><circle cx="13" cy="13" r="12" fill="#fff"/><rect x="9" y="6" width="8" height="14" rx="2" fill="#ff7f00"/></svg>
      <span>Knee Brace(s)</span></div>

    <div></div>
    <div class="options grey">
      <p class="option">Single Injection (Gelvia One)</p><p class="grade">OA Grade &nbsp;1,2,3,4</p>
      <p class="option">Single Injection (Duralite)</p><p class="grade">OA Grade &nbsp;1,2,3,4</p>
      <p class="option">3 Part Injection Series (Flexora)</p><p class="grade">OA Grade &nbsp;1,2,3,4</p>
      <p class="option plain" style="padding-left:8px">3/4 Part Injection Series (Jointvisc)</p><p class="grade option">OA Grade &nbsp;1,2,3,4</p>
    </div>
    <div class="options white">
      <p class="option">Single Injection (Plasmacel)</p><p class="grade">OA Grade &nbsp;1,2</p>
      <p class="option">2 Part Injection Series</p><p class="grade">OA Grade &nbsp;2,3</p>
    </div>
    <div class="options grey">
      <p class="option">Single Injection</p><p class="grade">OA Grade &nbsp;1,2,3,4</p>
    </div>
    <div class="options white" style="padding-left:20px">
      <p class="option plain">Kinetic 2</p><p class="grade flush">OA Grade &nbsp;1,2,3,4</p>
      <p class="option plain">Patellar Stabilization</p><p class="grade flush">OA Grade 1,2,3,4</p>
    </div>

    <div class="label"><span class="label-icon"><svg viewBox="0 0 60 30"><rect x="2" y="3" width="22" height="22" fill="#45d0c5"/><rect x="10" y="11" width="7" height="7" fill="#fff"/><path d="M30 14h8M34 10v8" stroke="#fff" stroke-width="2"/><path d="M44 24 L56 8" stroke="#45d0c5" stroke-width="6" stroke-linecap="round"/></svg></span>Cushion &amp; Lubricate</div>
    <div class="cell teal"><svg class="tick"><use href="#tick"/></svg></div>
    <div class="cell orange"><svg class="tick"><use href="#tick"/></svg></div>
    <div class="cell teal"><svg class="tick"><use href="#tick"/></svg></div>
    <div class="cell orange"></div>

    <div class="label"><span class="label-icon"><svg viewBox="0 0 60 30"><circle cx="15" cy="15" r="12" fill="none" stroke="#45d0c5" stroke-width="2"/><circle cx="15" cy="15" r="8" fill="none" stroke="#45d0c5" stroke-width="2"/><circle cx="15" cy="15" r="4" fill="none" stroke="#45d0c5" stroke-width="2"/></svg></span>Decrease Inflammation</div>
    <div class="cell teal"><svg class="tick"><use href="#tick"/></svg></div>
    <div class="cell orange"><svg class="tick"><use href="#tick"/></svg></div>
    <div class="cell teal"><svg class="tick"><use href="#tick"/></svg></div>
    <div class="cell orange"></div>

    <div class="label"><span class="label-icon"><svg viewBox="0 0 60 30"><rect x="3" y="13" width="6" height="14" fill="#45d0c5"/><path d="M11 13 L17 3 C20 3 20 7 19 11 H27 C29 11 29 15 27 15 C29 16 29 20 26 20 C28 21 27 25 24 25 H11 Z" fill="#45d0c5"/></svg></span>Stimulates Synovial<br>Production of HA</div>
    <div class="cell teal"><svg class="tick"><use href="#tick"/></svg></div>
    <div class="cell orange"><svg class="tick"><use href="#tick"/></svg></div>
    <div class="cell teal"><svg class="tick"><use href="#tick"/></svg></div>
    <div class="cell orange"></div>

    <div class="label"><span class="label-icon"><svg viewBox="0 0 60 30"><path d="M15 27 L3 14 C-1 8 5 1 11 5 L15 8 L19 5 C25 1 31 8 27 14 Z" fill="#45d0c5"/><path d="M15 10v9M10.5 14.5h9" stroke="#fff" stroke-width="2.4"/></svg></span>Healing Properties</div>
    <div class="cell teal"></div>
    <div class="cell orange"><svg class="tick"><use href="#tick"/></svg></div>
    <div class="cell teal"><svg class="tick"><use href="#tick"/></svg></div>
    <div class="cell orange"></div>

    <div class="label"><span class="label-icon"><svg viewBox="0 0 60 30"><path d="M4 27 L18 12" stroke="#45d0c5" stroke-width="4" stroke-linecap="round"/><circle cx="21" cy="8" r="6" fill="none" stroke="#45d0c5" stroke-width="3"/></svg></span>Repairative Properties</div>
    <div class="cell teal"></div>
    <div class="cell orange"></div>
    <div class="cell teal"><svg class="tick"><use href="#tick"/></svg></div>
    <div class="cell orange"></div>

    <div class="label"><span class="label-icon"><svg viewBox="0 0 60 30"><circle cx="18" cy="8" r="5" fill="#45d0c5"/><path d="M14 12 C10 16 10 22 12 29 M19 14 C16 18 17 23 18 29" stroke="#fff" stroke-width="1.5" fill="none"/></svg></span>Potential Cartilage<br>Regeneration</div>
    <div class="cell teal"></div>
    <div class="cell orange"><svg class="tick"><use href="#tick"/></svg></div>
    <div class="cell teal"><svg class="tick"><use href="#tick"/></svg></div>
    <div class="cell orange"></div>

    <div class="label"><span class="label-icon"><svg viewBox="0 0 60 30"><circle cx="15" cy="15" r="13" fill="#fff"/><path d="M15 2 A13 13 0 0 1 15 28 Z" fill="#45d0c5"/></svg></span>On Average, Benefits<br>Last 4-6 Months</div>
    <div class="cell teal"><svg class="tick"><use href="#tick"/></svg></div>
    <div class="cell orange"><svg class="tick"><use href="#tick"/></svg></div>
    <div class="cell teal"><svg class="tick"><use href="#tick"/></svg></div>
    <div class="cell orange"><svg class="tick"><use href="#tick"/></svg></div>

    <div class="label"><span class="label-icon"><svg viewBox="0 0 60 30"><circle cx="15" cy="15" r="13" fill="#45d0c5"/></svg></span>On Average, Benefits<br>Last 6-12 Months</div>
    <div class="cell teal"></div>
    <div class="cell orange"></div>
    <div class="cell teal"><svg class="tick"><use href="#tick"/></svg></div>
    <div class="cell orange"><svg class="tick"><use href="#tick"/></svg></div>

    <div class="label"><span class="label-icon"><svg viewBox="0 0 60 30"><circle cx="15" cy="15" r="13" fill="#45d0c5"/><path d="M37 15h6M40 12v6" stroke="#fff" stroke-width="1.4"/></svg></span>On Average, Benefits<br>Last 18+ Months</div>
    <div class="cell teal"></div>
    <div class="cell orange"></div>
    <div class="cell teal"><svg class="tick"><use href="#tick"/></svg></div>
    <div class="cell orange"><svg class="tick"><use href="#tick"/></svg></div>

    <div class="label"><span class="label-icon"><svg viewBox="0 0 60 30"><circle cx="18" cy="7" r="5" fill="#45d0c5"/><path d="M14 11 C10 15 10 21 12 29 M19 13 C16 17 17 22 18 29" stroke="#fff" stroke-width="1.5" fill="none"/><path d="M37 15h6M40 12v6" stroke="#fff" stroke-width="1.4"/></svg></span>Corrects Biomechanics<br>&amp; Stabilizes Joint</div>
    <div class="cell teal"></div>
    <div class="cell orange"></div>
    <div class="cell teal"></div>
    <div class="cell orange"><svg class="tick"><use href="#tick"/></svg></div>

    <div class="label"><span class="label-icon"><svg viewBox="0 0 60 30"><path d="M3 15 A13 12 0 0 1 29 15 Z" fill="#45d0c5"/><path d="M16 15v10 a2.5 2.5 0 0 1 -5 0" stroke="#45d0c5" stroke-width="2" fill="none"/></svg></span>Covered by MOST<br>Insurance</div>
    <div class="cell teal"><svg class="tick"><use href="#tick"/></svg></div>
    <div class="cell orange"></div>
    <div class="cell teal"></div>
    <div class="cell orange"><svg class="tick"><use href="#tick"/></svg></div>
  </section>

  <p class="disclaimer">Treatment outcomes vary by individual. Treatment benefits and<br>length of efficacy are not guaranteed. In some cases, patient’s do not<br>respond to treatment. Multiple treatments may be recommended or<br>necessary for the best outcomes.</p>
  <svg class="rule" viewBox="0 0 311 4" preserveAspectRatio="none"><path d="M0 2 Q155 -1 311 2 Q155 5 0 2 Z" fill="#ff7f00"/></svg>
</main>
</body>
</html>
```